Brell Stone Company Business Cards

Front and Back Business Card - logo and text setup - cool design. I need workable photoshop or illustrator files so I can setup each employee card with design that is created
Updates

Hi everyone, thank you for the great entries. Please no more white and blue cards - there are so many already - black and silver only now please. thanks!

Target Market(s)

Construction Industry - Facility Managers

Industry/Entity Type

Construction

Contact Information for Business Card

I really like contemporary simplistic looks - clean neat....not opposed to seeing some black backrounds

Requirements
Must have
• Logo/website address with design on front only - www.brellstone-example.com (logo attached)
• Back:
• Name/Title/Company Address/Phone/email address
Nice to have
• Cool design
Should not have
• Nothing gimmicky like Fire or Water - since we are a Fire Protection company - it has all been done

```html
<!DOCTYPE html>
<html lang="en">
<head>
<meta charset="utf-8">
<title>Brell Stone Company – Business Cards</title>
<link rel="stylesheet" href="https://fonts.googleapis.com/css2?family=Lato:wght@400;700&display=swap">
<style>
  :root {
    --backdrop: #1b1b1b;
    --card-black: #131313;
    --card-silver: #d4d4d6;
    --silver-bright: #dcdcde;
    --silver-mid: #a9a9ad;
    --ink-black: #141414;
    --ink-grey: #3a3a3c;
  }
  * { margin: 0; padding: 0; box-sizing: border-box; }
  html, body {
    width: 1200px;
    height: 800px;
    overflow: hidden;
    background: var(--backdrop);
    font-family: "Lato", sans-serif;
  }
  .canvas {
    position: relative;
    width: 1200px;
    height: 800px;
  }
  .card {
    position: absolute;
    top: 112px;
    width: 316px;
    height: 530px;
    display: flex;
    flex-direction: column;
    align-items: center;
    justify-content: center;
    padding-bottom: 58px;
  }
  .card--front {
    left: 258px;
    background: var(--card-black);
  }
  .card--back {
    left: 629px;
    background: var(--card-silver);
    text-align: center;
  }
  .brand {
    display: flex;
    align-items: center;
    gap: 10px;
  }
  .brand__mark {
    width: 14px;
    height: 14px;
    background: var(--silver-mid);
  }
  .brand__name {
    font-weight: 700;
    font-size: 34px;
    color: var(--silver-bright);
    letter-spacing: 0.5px;
  }
  .brand__web {
    margin-top: 14px;
    font-size: 14px;
    color: var(--silver-mid);
    letter-spacing: 0.5px;
  }
  .person__name {
    font-weight: 700;
    font-size: 30px;
    color: var(--ink-black);
    line-height: 1.1;
  }
  .person__title {
    font-weight: 700;
    font-size: 21px;
    color: var(--ink-grey);
    line-height: 1.25;
  }
  .divider {
    font-size: 14px;
    color: var(--ink-grey);
    letter-spacing: 1px;
    margin: 2px 0 14px;
  }
  .contact {
    font-size: 15px;
    color: var(--ink-grey);
    line-height: 1.4;
  }
  .contact--address { margin-top: 8px; }
</style>
</head>
<body>
  <main class="canvas">
    <section class="card card--front" aria-label="Card front">
      <div class="brand">
        <span class="brand__mark"></span>
        <span class="brand__name">Brell Stone</span>
      </div>
      <p class="brand__web">www.brellstone-example.com</p>
    </section>

    <section class="card card--back" aria-label="Card back">
      <p class="person__name">Daniel Marsh</p>
      <p class="person__title">CEO/Founder</p>
      <p class="divider">...........</p>
      <p class="contact">(555) 014-2869 | (555) 014-2866<br>
        info@brellstone-example.com<br>www.brellstone-example.com</p>
      <p class="contact contact--address">48 Quarry Lane, Unit 3,<br>Harlow Point, NY 10990</p>
    </section>
  </main>
</body>
</html>
```